larkforge website

commerce website to sell cookeries, brackets, mailboxes and to show off homes built. Modern Steel in design see marlo cycles web page to be like: https://www.marlocycles-demo.com/en/ sorry its bright nest hosting word press divi

must be able to add products to page

Target Market(s)

mainly western states of U.S.

Industry/Entity Type

Building Product

Coding

Coded - Design and coding required

Number of Pages Required

3 page

Font styles to use
Sans Serif

Colors

Designer to choose colors to be used in the design.

Requirements
Must have
• customers to be able to order products from page
• bright nest hosting word press divi

```html
<!DOCTYPE html>
<html lang="en">
<head>
<meta charset="utf-8">
<title>Larkforge – Product Details</title>
<link href="https://fonts.googleapis.com/css2?family=Poppins:wght@400;500;600&family=Rubik:wght@400;500&family=Roboto:wght@400;500;700&display=swap" rel="stylesheet">
<style>
:root{
  --brand:#445f8b;
  --search-btn:#5f7fb4;
  --page:#f5f5f5;
  --white:#ffffff;
  --ink:#222222;
  --text:#444444;
  --muted:#777777;
  --star:#f5a623;
  --line:#e2e2e2;
  --chip:#e9e9e9;
  --steel-light:#f1f2f4;
  --steel-mid:#d9dce1;
}
*{box-sizing:border-box;margin:0;padding:0}
html,body{width:785px;height:1200px;overflow:hidden;background:var(--page)}
.stage{width:1350px;height:2063px;transform:scale(0.58148);transform-origin:0 0;position:relative;background:var(--page);font-family:"Poppins",sans-serif;color:var(--text)}

/* header */
.site-header{position:absolute;left:0;top:0;width:1350px;height:137px;background:var(--brand);color:var(--white);font-family:"Rubik",sans-serif}
.brand{position:absolute;left:98px;top:40px;display:flex;align-items:center;gap:12px;font-family:"Rubik",sans-serif;font-weight:500;font-size:30px;letter-spacing:1px;color:var(--white)}
.brand .dot{width:22px;height:22px;border-radius:50%;background:var(--white)}
.main-nav{position:absolute;left:375px;top:24px;display:flex;gap:30px;font-size:15px}
.top-links{position:absolute;right:100px;top:26px;font-size:14px}
.search{position:absolute;left:377px;top:66px;width:485px;height:40px;background:var(--white);display:flex;align-items:center;font-size:12px;color:var(--muted)}
.search .cat{width:48px;text-align:center;border-right:1px solid var(--line);line-height:24px;font-size:11px;color:#555}
.search .field{padding-left:22px;flex:1}
.search .go{width:55px;height:40px;background:var(--search-btn);display:flex;align-items:center;justify-content:center}
.account{position:absolute;top:70px;display:flex;align-items:center;gap:10px;font-size:13px;line-height:16px}
.account small{display:block;font-size:13px;color:#d6dff0}
.account span{font-size:14px}

/* breadcrumb */
.crumb-bar{position:absolute;left:0;top:137px;width:1350px;height:70px;background:var(--white)}
.crumb-bar h1{position:absolute;left:100px;top:25px;font-family:"Rubik",sans-serif;font-weight:500;font-size:19px;letter-spacing:.5px;color:var(--ink)}
.crumb-bar nav{position:absolute;right:100px;top:26px;font-family:"Rubik",sans-serif;font-size:16px;color:var(--ink)}

/* product */
.gallery{position:absolute;left:100px;top:263px;width:564px;height:489px;background:var(--white);border-radius:8px}
.hero-shot{position:absolute;left:100px;top:62px;width:356px;height:260px;border-radius:6px;background:linear-gradient(160deg,var(--steel-light),var(--steel-mid))}
.thumb{position:absolute;top:362px;width:107px;height:97px;border:1px solid #dcdcdc;background:var(--white);padding:10px}
.thumb i{display:block;width:100%;height:100%;background:linear-gradient(160deg,var(--steel-light),var(--steel-mid))}
.info{position:absolute;left:712px;top:300px;width:540px}
.info h2{font-family:"Rubik",sans-serif;font-weight:500;font-size:30px;line-height:34px;letter-spacing:.5px;color:var(--ink)}
.stars{color:var(--star);letter-spacing:3px}
.price{position:absolute;left:712px;top:400px;font-family:"Roboto",sans-serif;font-size:27px;font-weight:500;color:var(--brand)}
.price s{color:var(--ink);font-size:23px;margin-left:6px}
.hurry{position:absolute;left:713px;top:434px;font-size:17px;color:var(--ink)}
.hurry b{font-weight:600}
.timer{position:absolute;left:1019px;top:404px;display:flex;gap:10px}
.timer div{width:50px;height:55px;border-radius:3px;background:var(--chip);text-align:center;color:var(--brand);font-size:18px;padding-top:7px;line-height:20px}
.timer div small{display:block;font-size:12px;color:#555;margin-top:2px}
.timer div.on{background:var(--brand);color:var(--white)}
.timer div.on small{color:var(--white)}
.lead{position:absolute;left:713px;top:478px;width:535px;font-size:13.8px;line-height:23px;color:var(--text)}
.opts{position:absolute;left:718px;top:591px;display:flex;align-items:center;font-family:"Roboto",sans-serif;font-size:14px;font-weight:700;color:var(--ink)}
.qty{margin-left:10px;width:90px;height:40px;border:1px solid var(--line);background:var(--white);display:flex;align-items:center;justify-content:space-around;font-weight:400;padding:0 10px}
.size{margin-left:8px;width:100px;height:40px;border:1px solid var(--line);background:var(--white);display:flex;align-items:center;justify-content:space-between;padding:0 12px;font-weight:400;color:#555}
.btn-primary{position:absolute;left:718px;top:652px;width:224px;height:49px;border-radius:3px;background:var(--brand);color:var(--white);font-family:"Rubik",sans-serif;font-weight:500;font-size:17px;letter-spacing:1px;display:flex;align-items:center;justify-content:center}

/* tabs */
.tabs{position:absolute;left:100px;top:820px;display:flex;font-family:"Rubik",sans-serif;font-weight:500;font-size:16px;letter-spacing:.5px;color:var(--ink)}
.tabs span{padding:0 13px 12px}
.tabs .active{color:var(--brand);border-bottom:3px solid var(--brand)}
.tab-body{position:absolute;left:100px;top:853px;width:1150px;height:171px;background:var(--white);padding:36px 37px;font-size:13.8px;line-height:23px}

/* related */
.related-title{position:absolute;left:0;top:1092px;width:1350px;text-align:center;font-family:"Roboto",sans-serif;font-weight:500;font-size:36px;color:var(--ink)}
.card{position:absolute;top:1156px;width:277px;height:392px;background:var(--white);border-radius:8px;text-align:center;font-family:"Roboto",sans-serif}
.card .pic{position:absolute;left:40px;top:36px;width:197px;height:168px;border-radius:4px;background:linear-gradient(160deg,var(--steel-light),var(--steel-mid))}
.card h3{position:absolute;left:0;top:212px;width:100%;font-weight:500;font-size:21px;line-height:21px;color:#333}
.card .cost{position:absolute;left:0;top:259px;width:100%;font-size:17px;font-weight:500;color:var(--ink)}
.card .cost b{color:var(--brand);font-size:20px}
.card .stars{position:absolute;left:0;top:286px;width:100%;font-size:18px}
.card .actions{position:absolute;left:0;top:316px;width:100%;display:flex;justify-content:center;gap:8px}
.fav{width:34px;height:36px;background:#dedede;display:flex;align-items:center;justify-content:center}
.btn-outline{width:122px;height:36px;border:2px solid var(--brand);color:var(--brand);font-weight:700;font-size:14px;display:flex;align-items:center;justify-content:center}

/* footer */
.site-footer{position:absolute;left:0;top:1644px;width:1350px;height:419px;background:var(--brand);color:var(--white);font-family:"Roboto",sans-serif}
.foot-brand{position:absolute;left:100px;top:180px;width:272px;text-align:center;font-size:14px;line-height:21px}
.foot-brand .brand{position:static;justify-content:center;font-size:38px;margin:-70px 0 22px}
.foot-col{position:absolute;top:102px;font-size:16px}
.foot-col h4{font-size:17px;font-weight:500;margin-bottom:12px;letter-spacing:.3px}
.foot-col li{list-style:none;line-height:28px;padding-left:4px}
.map-area{position:absolute;left:1020px;top:128px;width:220px;height:165px;border-radius:30px;background:radial-gradient(ellipse,rgba(255,255,255,.12),rgba(255,255,255,0) 70%)}
.contact p{display:flex;gap:8px;line-height:22px;margin-bottom:6px;font-size:15px}
.socials{display:flex;gap:16px;margin-top:10px;padding-left:2px}
.socials i{width:12px;height:12px;border-radius:50%;background:var(--white);display:block}
.foot-rule{position:absolute;left:100px;top:356px;width:1150px;height:1px;background:rgba(255,255,255,.15)}
.copy{position:absolute;left:100px;top:382px;font-weight:500;font-size:15px}
.legal{position:absolute;right:100px;top:382px;font-weight:500;font-size:15px}
.to-top{position:absolute;left:1280px;top:337px;width:38px;height:38px;border-radius:50%;background:var(--white);display:flex;align-items:center;justify-content:center}
</style>
</head>
<body>
<div class="stage">

<header class="site-header">
  <div class="brand"><i class="dot"></i>LARKFORGE</div>
  <nav class="main-nav"><span>Today's Deals</span><span>Help</span><span>Registry</span><span>Gift Cards</span><span>Sell</span></nav>
  <div class="top-links">One Request, Multiple Quotes &nbsp;|&nbsp; Shop Today's Deals</div>
  <div class="search">
    <div class="cat">ALL</div>
    <div class="field">Search for Products, Brands and More</div>
    <div class="go"><svg width="16" height="16" viewBox="0 0 16 16" fill="none" stroke="#fff" stroke-width="1.8"><circle cx="7" cy="7" r="5"/><path d="M11 11l4 4"/></svg></div>
  </div>
  <div class="account" style="left:883px">
    <svg width="30" height="32" viewBox="0 0 30 32" fill="none" stroke="#fff" stroke-width="2"><circle cx="15" cy="10" r="7"/><path d="M2 31c1-8 6-12 13-12s12 4 13 12"/></svg>
    <div><small>Sign In Join Free</small><span>Larkforge</span></div>
  </div>
  <div class="account" style="left:1037px">
    <svg width="28" height="34" viewBox="0 0 28 34" fill="none" stroke="#fff" stroke-width="2"><path d="M2 10h24v22H2z"/><path d="M9 13V7a5 5 0 0110 0v6"/></svg>
    <div><small>Order</small><span style="color:#d6dff0">Protection</span></div>
  </div>
  <div class="account" style="left:1147px">
    <svg width="34" height="30" viewBox="0 0 34 30" fill="none" stroke="#fff" stroke-width="2"><path d="M17 28S2 19 2 10a7.5 7.5 0 0115-2 7.5 7.5 0 0115 2c0 9-15 18-15 18z"/></svg>
    <div><small>0</small><span style="color:#d6dff0">Favorites</span></div>
  </div>
</header>

<section class="crumb-bar">
  <h1>PRODUCT DETAILS</h1>
  <nav>Home / Shop / product details</nav>
</section>

<section class="gallery">
  <div class="hero-shot" role="img" aria-label="Product photo: stainless steel divided dinner tray"></div>
  <div class="thumb" style="left:109px" role="img" aria-label="Product photo: steel cooking pot with lid"><i></i></div>
  <div class="thumb" style="left:224px" role="img" aria-label="Product photo: steel serving bowl"><i></i></div>
  <div class="thumb" style="left:339px" role="img" aria-label="Product photo: stacked steel tiffin set"><i></i></div>
</section>

<div class="info">
  <h2>DOZEN WHITE BOTANICAL LINEN DINNER NAPKINS</h2>
  <div class="stars" style="font-size:18px;margin-top:4px">★★★★★</div>
</div>
<div class="price">$70.00<s>$90.00</s></div>
<div class="hurry"><b>Hurry up!</b> offer ends in:</div>
<div class="timer">
  <div class="on">00<small>Days</small></div>
  <div>00<small>Hours</small></div>
  <div>00<small>Mins</small></div>
  <div>00<small>Secs</small></div>
</div>
<p class="lead">Lorem ipsum dolor sit amet, consetetur sadipscing elitr, sed diam nonumy eirmod tempor invidunt ut labore et dolore magna aliquyam erat, sed diam voluptua. Phasellus id nisi quis justo tempus mollis sed et dui. In hac habitasse platea dictumst.</p>
<div class="opts">
  QTY:<div class="qty"><span>-</span><span>1</span><span>+</span></div>
  <span style="margin-left:20px">SIZE :</span><div class="size"><span>S</span><svg width="10" height="6" viewBox="0 0 10 6" fill="none" stroke="#999"><path d="M1 1l4 4 4-4"/></svg></div>
</div>
<div class="btn-primary">ADD TO CART</div>

<nav class="tabs"><span class="active">DESCRIPTION</span><span>INFORMATION</span><span>REVIEWS (1)</span></nav>
<div class="tab-body">Lorem ipsum dolor sit amet, consectetur adipiscing elit. Nam fringilla augue nec est tristique auctor. Ipsum metus feugiat sem, quis fermentum turpis eros eget velit. Donec ac tempus ante. Fusce ultricies massa massa. Fusce aliquam, purus eget sagittis vulputate, sapien libero hendrerit est, sed commodo augue nisi non neque.Cras neque metus, consequat et blandit et, luctus a nunc. Etiam gravida vehicula tellus, in imperdiet ligula euismod eget. Pellentesque habitant morbi tristique senectus et netus et malesuada fames ac turpis egestas. Nam erat mi, rutrum at sollicitudin rhoncus</div>

<h2 class="related-title">RELATED PRODUCTS</h2>

<article class="card" style="left:100px">
  <div class="pic" role="img" aria-label="Product photo: wire sink basket"></div>
  <h3>Verano 30 Pieces<br>Dinnerware Set</h3>
  <div class="cost">Price: <b>$86.00</b></div>
  <div class="stars">★★★★★</div>
  <div class="actions"><div class="fav"><svg width="14" height="12" viewBox="0 0 14 12"><path d="M7 12S0 7 0 3.5A3.5 3.5 0 017 2a3.5 3.5 0 017 1.5C14 7 7 12 7 12z" fill="#555"/></svg></div><div class="btn-outline">ADD TO CART</div></div>
</article>
<article class="card" style="left:391px">
  <div class="pic" role="img" aria-label="Product photo: steel pan with long handle"></div>
  <h3>Verano 30 Pieces<br>Dinnerware Set</h3>
  <div class="cost">Price: <b>$86.00</b></div>
  <div class="stars">★★★★★</div>
  <div class="actions"><div class="fav"><svg width="14" height="12" viewBox="0 0 14 12"><path d="M7 12S0 7 0 3.5A3.5 3.5 0 017 2a3.5 3.5 0 017 1.5C14 7 7 12 7 12z" fill="#555"/></svg></div><div class="btn-outline">ADD TO CART</div></div>
</article>
<article class="card" style="left:679px">
  <div class="pic" role="img" aria-label="Product photo: wire sink basket"></div>
  <h3>Verano 30 Pieces<br>Dinnerware Set</h3>
  <div class="cost">Price: <b>$86.00</b></div>
  <div class="stars">★★★★★</div>
  <div class="actions"><div class="fav"><svg width="14" height="12" viewBox="0 0 14 12"><path d="M7 12S0 7 0 3.5A3.5 3.5 0 017 2a3.5 3.5 0 017 1.5C14 7 7 12 7 12z" fill="#555"/></svg></div><div class="btn-outline">ADD TO CART</div></div>
</article>
<article class="card" style="left:970px">
  <div class="pic" role="img" aria-label="Product photo: round divided steel plate"></div>
  <h3>Verano 30 Pieces<br>Dinnerware Set</h3>
  <div class="cost">Price: <b>$86.00</b></div>
  <div class="stars">★★★★★</div>
  <div class="actions"><div class="fav"><svg width="14" height="12" viewBox="0 0 14 12"><path d="M7 12S0 7 0 3.5A3.5 3.5 0 017 2a3.5 3.5 0 017 1.5C14 7 7 12 7 12z" fill="#555"/></svg></div><div class="btn-outline">ADD TO CART</div></div>
</article>

<footer class="site-footer">
  <div class="foot-brand">
    <div class="brand"><i class="dot"></i>LARKFORGE</div>
    Lorem ipsum dolor sit amet, consectetur adipisicing elit, sed do eiusmod .
  </div>
  <div class="foot-col" style="left:460px">
    <h4>INFORMATION</h4>
    <ul><li>My Account</li><li>Wishlist</li><li>About Us</li><li>Contact Us</li><li>Blog</li></ul>
  </div>
  <div class="foot-col" style="left:697px">
    <h4>QUICK LINKS</h4>
    <ul><li>Shipping policy</li><li>Size Chart</li><li>Login</li><li>My Account</li><li>Register</li></ul>
  </div>
  <div class="map-area" role="img" aria-label="Faint dotted world map"></div>
  <div class="foot-col contact" style="left:951px;width:290px">
    <h4>CONTACT US</h4>
    <p><svg width="12" height="14" viewBox="0 0 12 14" style="margin-top:4px;flex:none"><path d="M6 0a5 5 0 015 5c0 4-5 9-5 9S1 9 1 5a5 5 0 015-5z" fill="#fff"/><circle cx="6" cy="5" r="2" fill="#445f8b"/></svg>Your current address goes to here,120 example, country.</p>
    <p><svg width="12" height="12" viewBox="0 0 12 12" style="margin-top:5px;flex:none"><path d="M2 0l3 3-1.5 2a7 7 0 003.5 3.5L9 7l3 3-2 2C5 12 0 7 0 2z" fill="#fff"/></svg>(008) 555 014 2290</p>
    <p><svg width="13" height="10" viewBox="0 0 13 10" style="margin-top:6px;flex:none"><rect width="13" height="10" fill="#fff"/><path d="M0 0l6.5 5L13 0" fill="none" stroke="#445f8b"/></svg>hello@larkforge-demo.com</p>
    <div class="socials"><i></i><i></i><i></i><i></i><i></i><i></i></div>
  </div>
  <div class="foot-rule"></div>
  <div class="copy">© 2020 Larkforge | All Rights Reserved.</div>
  <div class="legal">PRIVACY POLICY - TERMS OF USE</div>
  <div class="to-top"><svg width="10" height="6" viewBox="0 0 10 6" fill="none" stroke="#333" stroke-width="1.8"><path d="M1 5l4-4 4 4"/></svg></div>
</footer>

</div>
</body>
</html>
```